Need a stunning home page for Car rental company

For a client, I need a slick and sumber home page design. It is a small, local car rental company, with a handful of cars available for rent.
Selling points: affordable lease, availability, always clean cars
The design should be:
- flat and modern
- no, or very few animations/sliders
- CTA: booking form for renting a car.
- 3 featured cars with images and facts (see website) with button to read more about the car.
- fullscreen background video can be an option
- main colour: #efba01
The site is under construction here:
http://solvikutleie.hammerlia.no/
Delivery requirements:
I need a layered & well organised PSD file delivered.

```html
<!DOCTYPE html>
<html lang="no">
<head>
<meta charset="utf-8">
<title>Solvik Utleie – Hjem</title>
<link href="https://fonts.googleapis.com/css2?family=Raleway:wght@500;600;700&family=Open+Sans:ital,wght@0,400;0,600;1,400&display=swap" rel="stylesheet">
<style>
:root{
  --brand:#efba01;
  --brand-dark:#d9a400;
  --nav:#474747;
  --ink:#333;
  --text:#555;
  --muted:#999;
  --line:#e4e4e4;
  --band:#f3f3f3;
  --card-head:#efefef;
  --footer:#3d3d3d;
}
*{box-sizing:border-box;margin:0;padding:0}
html,body{width:1200px;height:2242px;overflow:hidden}
body{position:relative;background:#fff;font-family:"Open Sans",Arial,sans-serif;color:var(--text)}
.abs{position:absolute}

/* top navigation */
.topnav{left:0;top:0;width:1200px;height:52px;background:var(--nav)}
.topnav ul{list-style:none;display:flex;position:absolute;left:93px;top:0;height:52px}
.topnav li{font:600 13px "Open Sans",sans-serif;color:#fff;padding:0 22px;line-height:52px;text-transform:uppercase}
.topnav li.active{background:var(--brand)}
.lang{top:0;height:52px;width:46px;border-left:1px solid #5a5a5a;display:flex;align-items:center;justify-content:center}
.lang span{width:16px;height:11px;display:block}

/* header */
.logo{left:93px;top:96px;font:700 34px "Raleway",sans-serif;color:#555;letter-spacing:1px;display:flex;align-items:center;gap:12px}
.logo i{width:14px;height:14px;background:var(--brand);border-radius:50%;display:block}
.callus{left:598px;top:106px;display:flex;gap:10px;align-items:center}
.callus .ic{width:28px;height:28px;border-radius:50%;background:var(--brand);display:flex;align-items:center;justify-content:center}
.callus small{display:block;font-size:10px;color:#666}
.callus strong{display:block;font:700 18px "Open Sans",sans-serif;color:var(--brand)}
.search{left:778px;top:110px;width:230px;height:29px;border:1px solid #ddd;border-radius:15px;font-size:10px;color:#aaa;padding:7px 12px}
.search svg{position:absolute;right:10px;top:7px}
.account{left:1023px;top:110px;width:84px;height:27px;background:var(--brand);border-radius:3px;color:#fff;font:700 9px "Open Sans",sans-serif;text-align:center;line-height:27px}

/* hero */
.hero{left:0;top:177px;width:1200px;height:645px;background:radial-gradient(ellipse at 20% 10%,#f8d66a 0%,#d99b23 30%,#7a5321 62%,#3b3022 100%)}
.play{left:548px;top:447px}
.dots{left:580px;top:776px;display:flex;gap:4px}
.dots b{width:8px;height:8px;border-radius:50%;background:#fff;display:block}
.dots b.on{background:var(--brand)}

.booking{left:93px;top:269px;width:333px;height:463px;background:#fff;box-shadow:0 2px 6px rgba(0,0,0,.3)}
.booking h2{height:50px;background:#6b6b6b;color:#fff;font:600 18px "Raleway",sans-serif;padding:0 16px;line-height:50px}
.field{position:absolute;left:16px;width:301px;height:40px;border:1px solid var(--line);font-size:12px;color:#999;display:flex;align-items:center}
.field .lab{width:88px;height:100%;background:#f1f1f1;display:flex;align-items:center;gap:6px;padding-left:10px;color:#666;font-size:13px}
.field .val{padding-left:12px;flex:1;display:flex;justify-content:space-between;padding-right:10px}
.booking .q{position:absolute;left:16px;top:180px;font-size:13px;color:#444}
.select{padding:0 10px;justify-content:space-between}
.book-btn{position:absolute;left:16px;top:399px;width:301px;height:44px;background:linear-gradient(#f6c91c,var(--brand-dark));color:#fff;font:700 17px "Raleway",sans-serif;text-align:center;line-height:44px;border-radius:2px}

/* intro */
.section-title{left:0;width:1200px;text-align:center;font:700 25px "Raleway",sans-serif;color:var(--ink);text-transform:uppercase}
.section-title span{color:var(--brand)}
.intro{left:160px;top:907px;width:880px;text-align:center;font-size:12.5px;line-height:20px;color:#aaa}

/* cars */
.car{top:1043px;width:314px;height:624px;background:#fff;box-shadow:0 1px 5px rgba(0,0,0,.22)}
.car .photo{height:224px}
.car h3{height:58px;background:var(--card-head);font:600 22px "Raleway",sans-serif;color:#333;padding:0 22px;line-height:58px}
.car .price{height:47px;display:flex;align-items:center;border-bottom:1px solid var(--line);color:var(--brand);font-size:14px;padding-left:24px}
.car .price b{margin-left:auto;width:94px;font-weight:700}
.specs{padding:9px 0 0 24px;border-bottom:1px solid var(--line);height:216px}
.specs div{display:flex;height:27.5px;align-items:center;font-size:12.5px}
.specs dt{width:200px;color:#888}
.specs dd{color:#333}
.car .more{position:absolute;left:61px;top:565px;width:191px;height:38px;background:var(--brand);color:#fff;font:700 10.5px "Open Sans",sans-serif;text-align:center;line-height:38px;border-radius:2px;text-transform:uppercase;box-shadow:0 2px 0 var(--brand-dark)}

/* testimonials */
.testimonials{left:0;top:1723px;width:1200px;height:249px;background:var(--band);border-top:1px solid #e6e6e6}
.quote{top:1770px;width:301px;height:90px;background:#fff;border:1px solid #e6e6e6;padding:12px 14px;font:italic 12.5px/20px "Open Sans",sans-serif;color:#aaa}
.quote:after{content:"";position:absolute;left:40px;bottom:-9px;width:14px;height:14px;background:#fff;border-right:1px solid #e6e6e6;border-bottom:1px solid #e6e6e6;transform:rotate(45deg)}
.person{top:1880px;display:flex;align-items:center;gap:16px}
.person .avatar{width:62px;height:62px;border-radius:50%;background:radial-gradient(circle at 50% 40%,#c9a48a,#5a4a3f)}
.person strong{display:block;font-weight:400;font-size:13px;color:#333}
.person small{display:block;font-size:12.5px;color:var(--brand)}

/* contact */
.contact h4{font:600 16px "Raleway",sans-serif;color:#333;text-transform:uppercase;margin-bottom:12px}
.contact p{font-size:13px;line-height:20px;color:#777}
.contact{top:2025px}
.socials{display:flex;gap:7px}
.socials span{width:33px;height:33px;border-radius:2px;display:block}

.bottombar{left:0;top:2141px;width:1200px;height:101px;background:var(--footer);color:#bbb;font-size:13px;text-align:center;line-height:101px}
.bottombar a{color:#ccc;text-decoration:none;margin-left:14px}
.bottombar .tag{position:absolute;right:40px;top:0;color:#ddd;font-size:12px}
</style>
</head>
<body>

<nav class="abs topnav">
  <ul>
    <li class="active">Hjem</li><li>Bilparken vår</li><li>Tjenester</li><li>Kontakt oss</li><li>Blog</li><li>Page templates</li><li>About us</li>
  </ul>
</nav>
<div class="abs lang" style="left:1014px"><span style="background:#c8283a"></span></div>
<div class="abs lang" style="left:1060px;border-right:1px solid #5a5a5a"><span style="background:#2b3f86"></span></div>

<header>
  <div class="abs logo"><i></i>SOLVIK UTLEIE</div>
  <div class="abs callus">
    <div class="ic"><svg width="14" height="14" viewBox="0 0 24 24"><path fill="#fff" d="M6.6 10.8a15 15 0 0 0 6.6 6.6l2.2-2.2a1 1 0 0 1 1-.25 11.4 11.4 0 0 0 3.6.57 1 1 0 0 1 1 1V20a1 1 0 0 1-1 1A17 17 0 0 1 3 4a1 1 0 0 1 1-1h3.5a1 1 0 0 1 1 1c0 1.25.2 2.45.57 3.57a1 1 0 0 1-.25 1z"/></svg></div>
    <div><small>Spørsmål? Ring oss</small><strong>40 12 34 56</strong></div>
  </div>
  <div class="abs search">Søk hele nettstedet
    <svg width="14" height="14" viewBox="0 0 24 24"><circle cx="10" cy="10" r="7" fill="none" stroke="#999" stroke-width="2"/><path d="M15 15l6 6" stroke="#999" stroke-width="2"/></svg>
  </div>
  <div class="abs account">MIN KONTO</div>
</header>

<section class="abs hero" role="img" aria-label="Sportsbil fotografert bakfra i varmt solnedgangslys"></section>
<svg class="abs play" width="104" height="104" viewBox="0 0 104 104" aria-hidden="true"><circle cx="52" cy="52" r="49" fill="none" stroke="#fff" stroke-width="5"/><path d="M40 32v40l33-20z" fill="#fff"/></svg>
<div class="abs dots"><b></b><b class="on"></b><b></b><b></b></div>

<form class="abs booking">
  <h2>A BOOKING FORM TO RENT A CAR</h2>
  <div class="field select" style="top:75px">Select a car type <span>▾</span></div>
  <div class="field" style="top:128px"><div class="lab"><svg width="10" height="14" viewBox="0 0 10 14"><path d="M5 0a5 5 0 0 0-5 5c0 4 5 9 5 9s5-5 5-9a5 5 0 0 0-5-5zm0 7a2 2 0 1 1 0-4 2 2 0 0 1 0 4z" fill="#999"/></svg>Pick-up</div><div class="val">Enter city name:</div></div>
  <p class="q">Need a different drop-off location?</p>
  <div class="field" style="top:218px"><div class="lab"><svg width="10" height="14" viewBox="0 0 10 14"><path d="M5 0a5 5 0 0 0-5 5c0 4 5 9 5 9s5-5 5-9a5 5 0 0 0-5-5zm0 7a2 2 0 1 1 0-4 2 2 0 0 1 0 4z" fill="#999"/></svg>Drop-off</div><div class="val">Enter city name:</div></div>
  <div class="field" style="top:274px"><div class="lab"><svg width="12" height="12" viewBox="0 0 12 12"><rect y="2" width="12" height="10" fill="#999"/><rect x="1" y="5" width="10" height="6" fill="#f1f1f1"/></svg>Pick-up</div><div class="val"><span>mm/dd/yyyy</span><span>Time:12:30pm</span></div></div>
  <div class="field" style="top:330px"><div class="lab"><svg width="12" height="12" viewBox="0 0 12 12"><rect y="2" width="12" height="10" fill="#999"/><rect x="1" y="5" width="10" height="6" fill="#f1f1f1"/></svg>Pick-off</div><div class="val"><span>mm/dd/yyyy</span><span>Time:12:30pm</span></div></div>
  <div class="book-btn">A BOOKING CAR HERE</div>
</form>

<h2 class="abs section-title" style="top:854px">Welcome to <span>Solvik Utleie</span></h2>
<p class="abs intro">Solvik Utleie er en bilpark på Strandby, og leier ut varebiler og personbiler til deg som trenger en ekstrabil til flytting, ferie, bytur eller hva det måtte være. Vi er uslåelige på service, og mest sannsynlig også på pris. Og du kan stole på at bilen du får fra oss er både ren og pen!</p>

<h2 class="abs section-title" style="top:985px">Featured <span>cars</span></h2>

<article class="abs car" style="left:93px">
  <div class="photo" role="img" aria-label="Hvit sedan parkert foran en murbygning" style="background:linear-gradient(160deg,#4a4540,#8c8a86 55%,#3a3836)"></div>
  <h3>Varebilen</h3>
  <div class="price">Pris per døgn<b>kr 600</b></div>
  <dl class="specs"><div><dt>Biltype</dt><dd>Varebil</dd></div><div><dt>Maks. pers.</dt><dd>2</dd></div><div><dt>Ant. dører</dt><dd>5</dd></div><div><dt>Min. sjåføralder</dt><dd>21</dd></div><div><dt>Girtype</dt><dd>Manuell</dd></div><div><dt>Klimaanlegg?</dt><dd>Ja</dd></div><div><dt>Ubegrenset km?</dt><dd>Nei</dd></div></dl>
  <div class="more">Read more about the car</div>
</article>
<article class="abs car" style="left:443px">
  <div class="photo" role="img" aria-label="Mørk SUV under skyet himmel" style="background:linear-gradient(180deg,#a9a2ae,#cfc9cf 45%,#3b3e44 75%,#6e6e6e)"></div>
  <h3>Varebilen</h3>
  <div class="price">Pris per døgn<b>kr 600</b></div>
  <dl class="specs"><div><dt>Biltype</dt><dd>Varebil</dd></div><div><dt>Maks. pers.</dt><dd>2</dd></div><div><dt>Ant. dører</dt><dd>5</dd></div><div><dt>Min. sjåføralder</dt><dd>21</dd></div><div><dt>Girtype</dt><dd>Manuell</dd></div><div><dt>Klimaanlegg?</dt><dd>Ja</dd></div><div><dt>Ubegrenset km?</dt><dd>Nei</dd></div></dl>
  <div class="more">Read more about the car</div>
</article>
<article class="abs car" style="left:793px">
  <div class="photo" role="img" aria-label="Sølvfarget terrengbil på gress" style="background:linear-gradient(180deg,#6f7b5c,#b4b8b6 50%,#8a9070 80%,#5d6a3f)"></div>
  <h3>Varebilen</h3>
  <div class="price">Pris per døgn<b>kr 600</b></div>
  <dl class="specs"><div><dt>Biltype</dt><dd>Varebil</dd></div><div><dt>Maks. pers.</dt><dd>2</dd></div><div><dt>Ant. dører</dt><dd>5</dd></div><div><dt>Min. sjåføralder</dt><dd>21</dd></div><div><dt>Girtype</dt><dd>Manuell</dd></div><div><dt>Klimaanlegg?</dt><dd>Ja</dd></div><div><dt>Ubegrenset km?</dt><dd>Nei</dd></div></dl>
  <div class="more">Read more about the car</div>
</article>

<section class="abs testimonials"></section>
<blockquote class="abs quote" style="left:93px">Lorem ipsum dolor sit amet, consectetur adipi-sicing elit, Aliquid consequuntur unde quae totam recusandae</blockquote>
<blockquote class="abs quote" style="left:450px">Lorem ipsum dolor sit amet, consectetur adipi-sicing elit, Aliquid consequuntur unde quae totam recusandae</blockquote>
<blockquote class="abs quote" style="left:806px">Lorem ipsum dolor sit amet, consectetur adipi-sicing elit, Aliquid consequuntur unde quae totam recusandae</blockquote>
<div class="abs person" style="left:93px"><div class="avatar" role="img" aria-label="Portrett av kunde"></div><div><strong>Mari Solheim</strong><small>CEO loremip</small></div></div>
<div class="abs person" style="left:450px"><div class="avatar" role="img" aria-label="Portrett av kunde"></div><div><strong>Mari Solheim</strong><small>CEO loremip</small></div></div>
<div class="abs person" style="left:806px"><div class="avatar" role="img" aria-label="Portrett av kunde"></div><div><strong>Mari Solheim</strong><small>CEO loremip</small></div></div>

<footer>
  <div class="abs contact" style="left:93px;width:220px"><h4>Address</h4><p>Solvik Utleie, Solvikveien 12, Strandby, Norge</p></div>
  <div class="abs contact" style="left:359px"><h4>Phone</h4><p>&nbsp;Spørsmål? Ring oss : 40 12 34 56</p></div>
  <div class="abs contact" style="left:654px"><h4>Email</h4><p>post@solvikutleie.no</p></div>
  <div class="abs contact" style="left:918px"><h4>Follow us</h4>
    <div class="socials"><span style="background:#3b5998"></span><span style="background:#1da1f2"></span><span style="background:#d34836"></span><span style="background:#0e76a8"></span><span style="background:#ea4c5a"></span></div>
  </div>
  <div class="abs bottombar">© Solvik Utleie 2014. All rights reserved. <a>Home</a><a>Configure</a><span class="tag">C4</span></div>
</footer>

</body>
</html>
```